Vantrel System Web Page Design

This project is to design 6 pages of a web based medical system for clinics, hospitals, drugs suppliers, general items suppliers, insurance company, laboratories and patients (basically all parties which could be involved in).We want the designs of the browser, button, icon and layout are based on Zeltor, which is user friendly, looks professional, simple and neat but with powerful functions. We have uploaded few pictures of another system, please do not copy its design because this is not what we are looking for, the pictures are for you to know the elements should be included in our pages. Vantrel web-base system, design 6 pages1. Login PageShould include the following elements-company id with input field-login id with input field-password with input field2. Main Page (Navigation page)Should include the following elements-Appointment-Consultation-Patient-Drugs inventory -General supplies inventory -Laboratory-Suppliers-Insurance-Reports 3. Appointment PageShould include all the the elements in the respective pictures plus the followings-Daily View, Weekly View, Monthly View buttons4. Consultation PageShould include all the the elements in the respective picture5. Patient Page5.1 General information Should include all the the elements in the respective picture5.2 medical history/lab reportsShould include all the the elements in the respective picture plus the followings-Notify patient button-Share report button.
Updated on 28 Nov:
Please stop using Harbor Suite in your designs which is not the name of our system. We have just rename our system to Vantrel, please take note.
We need the system to look professional not playful, do not use too many colors and playful icons.

```html
<!DOCTYPE html>
<html lang="en">
<head>
<meta charset="utf-8">
<title>Vantrel</title>
<link href="https://fonts.googleapis.com/css2?family=Fira+Sans:wght@300;400;500;600;700&family=Roboto:wght@300;400;500;700&display=swap" rel="stylesheet">
<style>
:root{
  --teal:#00bfcb;
  --teal-dark:#00a9b4;
  --orange:#f9a61c;
  --ink:#333;
  --muted:#777;
  --light:#f5f5f5;
  --field:#f1f1f1;
  --footer:#252525;
  --footer-line:#3a3a3a;
  --white:#fff;
}
*{box-sizing:border-box;margin:0;padding:0}
html,body{width:1200px;height:2624px;overflow:hidden}
body{font-family:"Roboto",sans-serif;color:var(--ink);background:var(--white);position:relative}
.abs{position:absolute}

/* top bar */
.topbar{position:absolute;left:0;top:0;width:1200px;height:28px;background:var(--teal);color:#fff;font-size:11px}
.topbar .phone{position:absolute;left:161px;top:7px;display:flex;align-items:center;gap:5px;font-weight:500}
.topbar .auth{position:absolute;left:888px;top:0;display:flex;height:28px}
.topbar .login{width:74px;background:#fff;color:#555;text-align:center;line-height:28px;font-size:10px;font-weight:500}
.topbar .signup{width:74px;background:var(--orange);color:#fff;text-align:center;line-height:28px;font-size:10px;font-weight:500}

/* header */
.header{position:absolute;left:0;top:28px;width:1200px;height:84px;background:#fff}
.brand{position:absolute;left:161px;top:22px;display:flex;align-items:center;gap:8px;font-family:"Fira Sans",sans-serif;font-weight:600;font-size:36px;color:var(--teal)}
.brand .dot{width:18px;height:18px;border-radius:50%;background:var(--teal)}
.nav{position:absolute;left:520px;top:0;display:flex;font-size:10px;font-weight:500;color:#555;text-transform:uppercase}
.nav a{display:block;height:56px;line-height:56px;padding:0 12px;color:inherit;text-decoration:none;margin-top:0}
.nav a.active{background:var(--teal);color:#fff;height:56px;padding:0 14px;border-radius:0 0 3px 3px}

/* hero */
.hero{position:absolute;left:0;top:112px;width:1200px;height:488px;background:linear-gradient(120deg,#dfe5e8 0%,#c9d2d6 40%,#b8c1c5 70%,#d9dfe2 100%)}
.hero-card{position:absolute;left:313px;top:259px;width:574px;height:178px;background:rgba(255,255,255,.85);border:4px solid rgba(255,255,255,.5);text-align:center;padding-top:30px}
.hero-card h1{font-family:"Fira Sans",sans-serif;font-weight:300;font-size:29px;color:#333}
.hero-card h1 b{font-weight:600}
.hero-card p{font-size:10.5px;color:#555;line-height:19px;margin:10px auto 0;width:490px}
.dots{display:flex;justify-content:center;gap:6px;margin-top:22px}
.dots i{width:10px;height:10px;border:1.5px solid var(--teal);border-radius:50%;display:block}
.dots i.on{background:var(--teal);box-shadow:inset 0 0 0 2px #fff}

/* section titles */
.sec-title{font-family:"Fira Sans",sans-serif;font-size:25px;text-align:center;display:flex;justify-content:center;align-items:center;gap:10px}
.sec-title::before,.sec-title::after{content:"";width:30px;height:2px;background:currentColor}
.sec-sub{font-size:10.5px;line-height:19px;text-align:center;margin-top:8px}

/* what we do */
.services{position:absolute;left:0;top:600px;width:1200px;height:525px;background:var(--teal);color:#fff}
.services .sec-title{margin-top:52px;font-weight:500}
.grid{position:absolute;left:297px;top:161px;width:606px;height:304px;display:grid;grid-template-columns:repeat(3,1fr);grid-template-rows:repeat(3,1fr);border:1px solid rgba(255,255,255,.6)}
.cell{border:1px solid rgba(255,255,255,.6);display:flex;flex-direction:column;align-items:center;justify-content:center;gap:10px;font-size:13px;color:#fff}
.cell svg{width:28px;height:28px;fill:none;stroke:#fff;stroke-width:1.5}
.cell.active{background:#fff;color:#444}
.cell.active svg{stroke:var(--orange)}

/* who we are */
.about{position:absolute;left:0;top:1125px;width:1200px;height:440px;background:var(--light)}
.about-photo{position:absolute;left:161px;top:-14px;width:352px;height:467px;background:#fff;padding:8px;box-shadow:0 2px 8px rgba(0,0,0,.15)}
.about-photo .fill{width:100%;height:100%;background:linear-gradient(180deg,#dfe3ea 0%,#c8cfdc 55%,#b5bdcc 100%);position:relative}
.about-photo .fill::after{content:"";position:absolute;left:14px;top:14px;right:14px;bottom:14px;border:1px solid rgba(255,255,255,.8)}
.about-text{position:absolute;left:610px;top:57px;width:430px}
.about-text h2{font-family:"Fira Sans",sans-serif;font-weight:400;font-size:25px;display:flex;align-items:center;gap:10px}
.about-text h2::before{content:"";width:30px;height:2px;background:var(--teal)}
.about-text h3{font-family:"Fira Sans",sans-serif;font-weight:500;font-size:16px;line-height:21px;color:#444;margin-top:26px}
.about-text p{font-size:10.5px;line-height:19px;color:#666;margin-top:14px}

/* contact band */
.contact-band{position:absolute;left:0;top:1565px;width:1200px;height:220px;background:var(--orange);color:#fff}
.contact-band .sec-title{margin-top:68px;font-weight:300}
.contact-band .sec-title b{font-weight:700}
.wave{position:absolute;left:0;top:1715px;width:1200px;height:80px}

/* contact details */
.contact-info{position:absolute;left:236px;top:1848px;width:236px}
.contact-info h4{font-family:"Fira Sans",sans-serif;font-size:15px;font-weight:600;color:var(--teal);letter-spacing:.5px}
.contact-info .block{padding-bottom:14px;border-bottom:1px solid #e5e5e5;margin-bottom:18px}
.contact-info .block:last-child{border:0}
.social{display:flex;gap:12px;margin-top:6px}
.social i{width:13px;height:13px;border-radius:50%;background:#b8b8b8;display:block}
.social i:first-child{background:var(--orange)}
.contact-info p{font-size:10px;color:#888;line-height:16px;margin-top:6px}

.form{position:absolute;left:610px;top:1848px;width:354px}
.form h4{font-family:"Fira Sans",sans-serif;font-size:15px;font-weight:400;color:#333}
.form h4 b{font-weight:700}
.form .lead{font-size:10.5px;color:#777;line-height:17px;margin-top:8px;width:270px}
.field{background:var(--field);height:30px;font-size:10px;color:#888;display:flex;align-items:center;gap:6px;padding-left:10px;margin-top:8px}
.row{display:flex;gap:8px;margin-top:16px}
.row .field{flex:1;margin-top:0}
.field.msg{height:78px;align-items:flex-start;padding-top:10px}
.field svg{width:10px;height:10px;fill:none;stroke:#888;stroke-width:1.4}
.btn-submit{margin-top:16px;width:84px;height:30px;background:var(--teal);color:#fff;font-size:10px;font-weight:700;letter-spacing:1px;display:flex;align-items:center;justify-content:center;border-radius:2px}

/* footer */
.footer{position:absolute;left:0;top:2210px;width:1200px;height:365px;background:var(--footer);color:#fff}
.fcol{position:absolute;top:58px}
.fcol h5{font-family:"Fira Sans",sans-serif;font-weight:600;font-size:14px}
.fcol h5::after{content:"";display:block;width:24px;height:2px;background:var(--teal);margin-top:9px}
.fcol p{font-size:10px;line-height:21px;margin-top:14px;color:#eee}
.fcol ul{list-style:none;margin-top:8px}
.fcol li{font-size:10px;line-height:26.3px;color:#eee}
.fcol .more{font-size:10px;color:var(--orange);font-weight:700;margin-top:6px}
.sub-field{margin-top:14px;width:204px;height:30px;border:1px solid #888;display:flex;align-items:center;gap:8px;padding-left:10px;font-size:10px;color:#ddd}
.sub-field svg{width:11px;height:9px;fill:none;stroke:#ddd;stroke-width:1.3}
.sub-btn{margin-top:16px;width:76px;height:30px;background:#fff;color:var(--teal);font-size:9.5px;font-weight:700;letter-spacing:1px;display:flex;align-items:center;justify-content:center}
.bottom{position:absolute;left:0;top:2575px;width:1200px;height:49px;background:var(--footer);border-top:1px solid var(--footer-line);color:#ddd;font-size:10px}
.bottom .copy{position:absolute;left:161px;top:20px}
.bottom .copy span{color:var(--orange)}
.bottom .credit{position:absolute;right:161px;top:20px}
</style>
</head>
<body>

<div class="topbar">
  <div class="phone">
    <svg width="10" height="10" viewBox="0 0 10 10"><path d="M2 1l2 2-1 1.2c.6 1.2 1.6 2.2 2.8 2.8L7 6l2 2-1.2 1.2C4.5 9 1 5.5.8 2.2z" fill="#fff"/></svg>
    Call Us: (852) 5550 0142
  </div>
  <div class="auth"><div class="login">LOGIN</div><div class="signup">SIGN UP</div></div>
</div>

<header class="header">
  <div class="brand"><span class="dot"></span>Vantrel</div>
  <nav class="nav">
    <a class="active">Home</a><a>Appointment</a><a>Patient Info</a><a>Lab Reports</a><a>Consultation</a><a>Contact Us</a>
  </nav>
</header>

<section class="hero" role="img" aria-label="Photo of a clinician measuring a patient's blood pressure beside a stethoscope and clipboard">
  <div class="hero-card">
    <h1>World class <b>Healthcare</b> where you live.</h1>
    <p>Lorem ipsum dolor sit amet, consectetur adipiscing elit, sed do eiusmod tempor incididunt ut labore et dolore magna aliqua. Ut enim ad minim veniam, quis nostrud exercitation</p>
    <div class="dots"><i></i><i class="on"></i><i></i></div>
  </div>
</section>

<section class="services">
  <h2 class="sec-title">WHAT WE DO</h2>
  <p class="sec-sub">Lorem ipsum dolor sit amet, consectetur adipiscing elit, sed do eiusmod tempor incididunt ut labore et dolore magna aliqua<br>Ut enim ad minim veniam, quis nostrud exercitation ullamco laboris nisi</p>
  <div class="grid">
    <div class="cell"><svg viewBox="0 0 28 28"><rect x="4" y="6" width="20" height="18" rx="1"/><path d="M4 11h20M9 3v5M19 3v5M8 15h2M13 15h2M18 15h2M8 19h2M13 19h2M18 19h2"/></svg>Appointment</div>
    <div class="cell active"><svg viewBox="0 0 28 28"><path d="M4 8h13v8H9l-4 3v-3H4zM19 12h5v8h-1v3l-4-3h-6v-2"/></svg>Consultation</div>
    <div class="cell"><svg viewBox="0 0 28 28"><path d="M3 8v14M3 18h22v4M25 18v-4a2 2 0 0 0-2-2H12v6"/><circle cx="8" cy="14" r="2"/></svg>Patient</div>
    <div class="cell"><svg viewBox="0 0 28 28"><rect x="6" y="10" width="11" height="14" rx="2"/><path d="M7 6h9v4H7zM9 17h5M11.5 14.5v5"/><circle cx="21" cy="20" r="3.5"/></svg>Drugs Inventory</div>
    <div class="cell"><svg viewBox="0 0 28 28"><path d="M20 4l4 4M22 6l-3 3M19 9l-11 11-3-3L16 6zM5 23l3-3M11 11l2 2M14 8l2 2"/></svg>General Supplies Inventory</div>
    <div class="cell"><svg viewBox="0 0 28 28"><path d="M11 4h6M12 4v8l-6 11h16l-6-11V4M9 17h10"/></svg>Laboratory</div>
    <div class="cell"><svg viewBox="0 0 28 28"><path d="M3 6h4l3 12h12l2-9H9"/><circle cx="12" cy="22" r="1.6"/><circle cx="20" cy="22" r="1.6"/></svg>Suppliers</div>
    <div class="cell"><svg viewBox="0 0 28 28"><path d="M14 3l9 4v6c0 6-4 10-9 12-5-2-9-6-9-12V7zM14 10v8M10 14h8"/></svg>Insurance</div>
    <div class="cell"><svg viewBox="0 0 28 28"><rect x="6" y="5" width="16" height="20" rx="1"/><path d="M11 3h6v4h-6zM10 12h8M10 16h8M10 20h5"/></svg>Reports</div>
  </div>
</section>

<section class="about">
  <div class="about-photo"><div class="fill" role="img" aria-label="Photo of a doctor in a white coat with a stethoscope"></div></div>
  <div class="about-text">
    <h2>WHO&nbsp;<b>WE ARE</b></h2>
    <h3>Sed ut perspiciatis unde omnis iste natus error sit volupta tem accusantium doloremque</h3>
    <p>laudantium, totam rem aperiam, eaque ipsa quae ab illo inventore veritatis et quasi architecto beatae vitae dicta sunt explicabo. Nemo enim ipsam voluptatem quia voluptas sit aspernatur aut odit aut fugit, sed quia consequuntur magni dolores eos qui ratione voluptatem sequi nesciunt. Neque porro quisquam est, qui dolorem ipsum quia dolor sit amet, consectetur, adipisci velit, sed quia non numquam eius modi tempora</p>
    <p>Ut enim ad minima veniam, quis nostrum exercitationem ullam corporis suscipit laboriosam, nisi ut aliquid ex ea commodi consequatur. Quis autem vel eum iure reprehenderit qui in ea voluptate velit esse quam nihil molestiae consequatur</p>
    <p>Duis aute irure dolor in reprehenderit in voluptate velit esse cillum dolore eu fugiat nulla pariatur. Excepteur sint occaecat cupidatat non proident,</p>
  </div>
</section>

<section class="contact-band">
  <h2 class="sec-title">CONTACT&nbsp;<b>US</b></h2>
  <p class="sec-sub">Lorem ipsum dolor sit amet, consectetur adipiscing elit, sed do eiusmod tempor incididunt ut labore et dolore magna aliqua<br>Ut enim ad minim veniam, quis nostrud exercitation ullamco laboris nisi</p>
</section>
<svg class="wave" viewBox="0 0 1200 80" preserveAspectRatio="none" aria-hidden="true">
  <path fill="#f9a61c" d="M0 0H1200V34c-30 0-40 22-70 22s-40-30-80-30-40 26-80 26-50-24-90-24-40 30-90 30-50-36-100-36-40 30-90 30-40-20-80-20-50 30-100 30-50-40-100-40-40 26-80 26-40-22-80-22-40 28-90 28S60 20 30 22 0 60 0 60z"/>
</svg>

<div class="contact-info">
  <div class="block">
    <h4>FOLLOW US</h4>
    <div class="social"><i></i><i></i><i></i><i></i></div>
  </div>
  <div class="block">
    <h4>ADDRESS</h4>
    <p>Sed ut perspiciatis unde omnis iste natus error sit voluptatem accusantium</p>
  </div>
  <div class="block">
    <h4>CONTACT US</h4>
    <p>+100 555 0199<br>hello@vantrel.test</p>
  </div>
</div>

<div class="form">
  <h4>GET IN <b>TOUCH</b></h4>
  <p class="lead">Please complete and submit this form and one of our representatives will reply promptly</p>
  <div class="row">
    <div class="field"><svg viewBox="0 0 10 10"><circle cx="5" cy="3" r="2"/><path d="M1 10c0-3 2-4 4-4s4 1 4 4"/></svg>Your Name</div>
    <div class="field"><svg viewBox="0 0 10 10"><rect x=".7" y="2" width="8.6" height="6"/><path d="M1 2l4 3 4-3"/></svg>Your Email</div>
  </div>
  <div class="field"><svg viewBox="0 0 10 10"><path d="M2 1h4l2 2v6H2zM3.5 5h3M3.5 7h3"/></svg>Subject</div>
  <div class="field msg"><b style="color:#888">?</b>Message</div>
  <div class="btn-submit">SUBMIT</div>
</div>

<footer class="footer">
  <div class="fcol" style="left:161px;width:230px">
    <h5>About US</h5>
    <p>Lorem ipsum dolor sit amet, consectetur adipiscing elit, sed do eiusmod tempor incididunt ut labore et dolore magna aliqua. Ut enim ad minim veniam, quis nostrud exercitation ullamco laboris nisi ut aliquip ex ea commodo consequat. Duis aute irure dolor in reprehenderit in voluptate velit esse cillum dolore</p>
    <div class="more">Read More</div>
  </div>
  <div class="fcol" style="left:460px">
    <h5>Quick Links</h5>
    <ul><li>Home</li><li>Appointment</li><li>Patient Info</li><li>Lab Reports</li><li>Consultation</li><li>Contact Us</li></ul>
  </div>
  <div class="fcol" style="left:610px">
    <h5>Services</h5>
    <ul><li>Appointment</li><li>Consultation</li><li>Patient</li><li>Drugs inventory</li><li>General supplies inventory</li><li>Laboratory</li><li>Suppliers</li><li>Insurance</li><li>Reports</li></ul>
  </div>
  <div class="fcol" style="left:834px;width:210px">
    <h5>Subscribe Us</h5>
    <p style="line-height:17px">Subscribe to our Newsletter! to get latest news and updates regarding health</p>
    <div class="sub-field"><svg viewBox="0 0 11 9"><rect x=".7" y=".7" width="9.6" height="7.6"/><path d="M1 1l4.5 4L10 1"/></svg>Your email Address</div>
    <div class="sub-btn">SUBMIT</div>
  </div>
</footer>
<div class="bottom">
  <div class="copy">© 2018 <span>Vantrel</span>. All rights reserved.</div>
  <div class="credit">Design By Northfield Studio</div>
</div>

</body>
</html>
```